packaging design for disposable trash bag

We need 3 design for 3 of our products. first item is trash bag,the second item is disposable table cover and third is food packaging bag . We are a company in Singapore selling disposable product. This packaging products will be sold on shelf or online.

Attached is the requirement of the product. And some samples.

Target Market(s)

adult, most likely housewife

Requirements
Must have
• Packing design requirement for trash bag
• 1. Include company logo design, which is attached in the creative brief. DARVELLO POLYMER.
• 2. Clear showing of the product and its illustration of using. Eg. The trash bin.
• 3. Allocate a box for the purpose of sticking product size sticker.
• 4. Each packing bag holds 10pcs
• 5. Show of country of origin. Product of Singapore.
• 6. Use of one colour for printing of packing bag ( Black / blue/ bright Green/ white )
• 7. Show of warning: Keep polythene bags away from young children
• 8. dimension of the packagaing printing area : Lenght : 20 cm , Height 26 cm
• Packing design requirement for disposable Table Cover
• 1. Include company logo design, which is attached in the creative brief. Our company is DARVELLO POLYMER.
• 2. Clear showing of the product and its illustration of using. Eg. The table?.
• 4. Each packing bag holds 5pcs
• 6. Use of one colour for printing of the packing bag ( Black / blue/ bright Green )
• Packing design requirement for disposable food packaging plastic bag
• 2. Clear showing of the product and its illustration of using. Eg. Food?.
• 4. Show of country of origin. Product of Singapore.
• 5. Use of one colour for printing of the packing bag ( Black/ bright green )
• 6. Show of warning: Keep polythene bags away from young children
• 7. Show of product information: hygienic, food grade, freezer resistance, grease proof, damp proof, heat resistant.
• 8. Include the open here packing opening.
• 9. dimension of the packagaing printing area : Lenght : 15 cm , Height 22 cm
Nice to have
• requirement is stated in the must have. Good to allocate some space beside the packaging PCS area for promotion stickers . And also space allocated for bar code stickers.
Should not have
• no more than one color for printing

```html
<!DOCTYPE html>
<html lang="en">
<head>
<meta charset="utf-8">
<title>Disposable Food Packaging Plastic Bag</title>
<link rel="stylesheet" href="https://fonts.googleapis.com/css2?family=Big+Shoulders+Display:wght@200&family=Bebas+Neue&family=Oswald:wght@400;600&family=Roboto:wght@500&display=swap">
<style>
  :root {
    --ink: #111111;
    --brand-green: #1f9a3e;
    --paper-light: #ffffff;
    --paper-edge: #a9a9a9;
    --placeholder: #3a3a3a;
  }
  * { margin: 0; padding: 0; box-sizing: border-box; }
  html, body { width: 801px; height: 1200px; overflow: hidden; }
  body {
    position: relative;
    background: radial-gradient(ellipse 70% 60% at 50% 48%, var(--paper-light) 45%, var(--paper-edge) 100%);
    color: var(--ink);
    font-family: "Oswald", sans-serif;
  }
  .label-frame {
    position: absolute;
    left: 14px; top: 57px;
    width: 772px; height: 971px;
    border: 4px solid var(--ink);
    border-radius: 14px;
  }
  .top-rule {
    position: absolute;
    left: 32px; top: 90px;
    width: 725px; height: 3px;
    background: var(--ink);
  }
  .brand {
    position: absolute;
    left: 0; top: 128px; width: 801px;
    text-align: center;
    font-family: "Roboto", sans-serif;
    font-weight: 500;
    color: var(--brand-green);
    font-size: 15px;
    line-height: 17px;
  }
  .brand-square {
    display: block;
    width: 36px; height: 36px;
    margin: 0 auto 18px;
    background: var(--brand-green);
  }
  .food-illustration {
    position: absolute;
    left: 272px; top: 272px;
    width: 242px; height: 196px;
    background: var(--placeholder);
    border-radius: 40px 40px 20px 20px;
  }
  .title { position: absolute; left: 0; width: 801px; text-align: center; line-height: 1; }
  .title-thin {
    font-family: "Big Shoulders Display", sans-serif;
    font-weight: 200;
    font-size: 76px;
    letter-spacing: 1px;
  }
  .title-disposable { top: 496px; }
  .title-main {
    top: 590px;
    font-family: "Bebas Neue", sans-serif;
    font-size: 104px;
    letter-spacing: 2px;
  }
  .title-bag { top: 688px; }
  .size-rule {
    position: absolute;
    left: 293px; width: 215px; height: 3px;
    background: var(--ink);
  }
  .size-rule--top { top: 808px; }
  .size-rule--bottom { top: 985px; }
  .size-label {
    position: absolute;
    left: 0; top: 818px; width: 801px;
    text-align: center;
    font-family: "Bebas Neue", sans-serif;
    font-size: 36px;
    letter-spacing: 1px;
  }
  .disposal-icon {
    position: absolute;
    left: 70px; top: 825px;
    width: 112px; height: 138px;
    background: var(--placeholder);
    border-radius: 6px;
  }
  .recycle-icon {
    position: absolute;
    left: 616px; top: 838px;
    width: 112px; height: 112px;
  }
  .footer { position: absolute; left: 0; width: 801px; text-align: center; line-height: 1; }
  .footer-material { top: 1060px; font-weight: 600; font-size: 22px; }
  .footer-origin { top: 1094px; font-size: 27px; }
  .footer-warning { top: 1134px; font-size: 21px; letter-spacing: 2px; }
  .footer-warning strong { font-weight: 600; font-size: 25px; letter-spacing: 0; }
</style>
</head>
<body>
  <div class="label-frame"></div>
  <div class="top-rule"></div>

  <div class="brand">
    <span class="brand-square"></span>
    DARVELLO POLYMER<br>PTE LTD
  </div>

  <div class="food-illustration" role="img" aria-label="Black illustration of a burger, sandwich wedge and chicken drumstick"></div>

  <h1 class="title title-thin title-disposable">DISPOSABLE</h1>
  <div class="title title-main">FOOD PACKAGING</div>
  <div class="title title-thin title-bag">PLASTIC BAG</div>

  <div class="size-rule size-rule--top"></div>
  <div class="size-label">SIZE:</div>
  <div class="size-rule size-rule--bottom"></div>

  <div class="disposal-icon" role="img" aria-label="Icon of a person dropping litter into a bin"></div>

  <svg class="recycle-icon" viewBox="-56 -56 112 112" role="img" aria-label="Recycling symbol">
    <g fill="var(--ink)">
      <polygon points="-40,30 12,30 12,44 36,22 12,0 12,14 -30,14" />
      <polygon points="-40,30 12,30 12,44 36,22 12,0 12,14 -30,14" transform="rotate(120)" />
      <polygon points="-40,30 12,30 12,44 36,22 12,0 12,14 -30,14" transform="rotate(240)" />
    </g>
  </svg>

  <p class="footer footer-material">100% RECYKLED MATERIALS</p>
  <p class="footer footer-origin">PRODUCT OF SINGAPORE</p>
  <p class="footer footer-warning"><strong>WARNING:</strong> KEEP POLYTHENE BAGS AWAY FROM YOUNG CHILDREN</p>
</body>
</html>
```